Square V Dental Appointment Cards

This is a sister company of Tamarind Dental Group
We are a returning client.
This is what we like:
We like Parvell
Parvell font is cool
our Client is mostly Hispanic
We like to put Dr. Okafor, WMSU Graduate
Please look at Tamarind Dental Appt. Cards/Business Cards
Updates

We would like to see new logos, too.

Industry/Entity Type

Dental

Contact Information for Business Card

Tobi R. Okafor, D.D.S
WMSU Graduate
2836 West Larkspur Ave., Suite 410
Anaheim, CA 92817

Colors

Designer to choose colors to be used in the design.

Requirements
Nice to have
• Parvell Features

```html
<!DOCTYPE html>
<html lang="en">
<head>
<meta charset="UTF-8">
<title>Square V Dental – Appointment Cards</title>
<link rel="stylesheet" href="https://fonts.googleapis.com/css2?family=Lato:wght@400;700&display=swap">
<style>
  :root {
    --blue: #2f95d3;
    --orange: #f59a12;
    --paper: #eeeeee;
    --disc: rgba(246, 246, 246, 0.92);
    --ink: #2b2b2b;
    --muted: #a9a9a9;
    --rule: #555555;
    --white: #ffffff;
    --backdrop: #e9e6e3;
  }
  * { box-sizing: border-box; margin: 0; padding: 0; }
  html, body {
    width: 1200px; height: 900px; overflow: hidden;
    background: var(--backdrop);
    font-family: "Lato", Arial, sans-serif;
  }
  .canvas { position: relative; width: 1200px; height: 900px; }

  .card { position: absolute; overflow: hidden; }

  /* Front card */
  .card--front {
    left: 78px; top: 34px; width: 587px; height: 364px;
    background: linear-gradient(to right, var(--blue) 0 387px, var(--orange) 387px 100%);
    color: var(--white);
  }
  .doctor { position: absolute; left: 31px; top: 50px; line-height: 1.15; }
  .doctor__name { font-weight: 700; font-size: 17px; letter-spacing: 0.2px; }
  .doctor__school { font-size: 17px; }
  .phone {
    position: absolute; left: 31px; top: 124px;
    display: flex; align-items: center; gap: 8px; font-size: 18px;
  }
  .address { position: absolute; left: 31px; top: 273px; font-size: 17px; line-height: 1.32; }

  .disc {
    position: absolute; border-radius: 50%; background: var(--disc);
    display: flex; flex-direction: column; align-items: center; justify-content: center; gap: 16px;
  }
  .card--front .disc { left: 230px; top: 23px; width: 320px; height: 320px; }

  .brand { display: flex; flex-direction: column; align-items: center; gap: 18px; }
  .brand__dot { width: 74px; height: 74px; border-radius: 50%; border: 3px solid var(--orange); }
  .brand__name { font-weight: 700; font-size: 30px; color: var(--blue); letter-spacing: 0.5px; }
  .brand--faint { opacity: 0.45; }

  /* Back card */
  .card--back {
    left: 389px; top: 505px; width: 566px; height: 352px;
    background: linear-gradient(to right, var(--orange) 0 209px, var(--paper) 209px 100%);
    color: var(--ink);
  }
  .card--back .disc { left: 52px; top: 20px; width: 310px; height: 310px; }

  .appointment { position: absolute; right: 26px; top: 48px; font-size: 15px; letter-spacing: 0.2px; }
  .field {
    position: absolute; left: 369px; width: 172px;
    border-bottom: 1px solid var(--rule);
    text-align: right; font-size: 15px; color: var(--muted); padding-bottom: 2px;
  }
  .field--date { top: 178px; }
  .field--time { top: 220px; }
  .notice {
    position: absolute; right: 26px; top: 272px;
    text-align: right; font-size: 14px; line-height: 1.5;
  }
</style>
</head>
<body>
<main class="canvas">

  <section class="card card--front" aria-label="Business card, front">
    <div class="doctor">
      <p class="doctor__name">TOBI R. OKAFOR, D.D.S</p>
      <p class="doctor__school">WMSU Graduate</p>
    </div>
    <p class="phone">
      <svg width="22" height="22" viewBox="0 0 22 22" aria-hidden="true">
        <circle cx="11" cy="11" r="9.5" fill="none" stroke="#fff" stroke-width="1.6"/>
        <path d="M8 6.2c.6-.4 1.2-.2 1.5.4l.8 1.6c.2.5.1 1-.3 1.3l-.6.5c.5 1.2 1.4 2.1 2.6 2.6l.5-.6c.3-.4.8-.5 1.3-.3l1.6.8c.6.3.8.9.4 1.5-.6 1-1.7 1.4-2.8 1-2.6-.9-4.6-2.9-5.5-5.5-.4-1.1 0-2.2.5-2.9z" fill="#fff"/>
      </svg>
      <span>000 555 0000</span>
    </p>
    <address class="address" style="font-style:normal">
      2836 West Larkspur Ave.,<br>Suite 410 Anaheim, CA 92817
    </address>
    <div class="disc">
      <div class="brand">
        <span class="brand__dot"></span>
        <span class="brand__name">Square V Dental</span>
      </div>
    </div>
  </section>

  <section class="card card--back" aria-label="Appointment card, back">
    <div class="disc">
      <div class="brand brand--faint">
        <span class="brand__dot"></span>
        <span class="brand__name">Square V Dental</span>
      </div>
    </div>
    <p class="appointment">YOUR NEXT APPOINTMENT</p>
    <p class="field field--date">Date</p>
    <p class="field field--time">Time</p>
    <p class="notice">If unable to keep appointment<br>kindly give 24hrs notice</p>
  </section>

</main>
</body>
</html>
```